Business Card Design for company

We want new business cards. We'd like something different-- yet still highly professional. Our tagline is Providing leadership, delivering success. Stock photos are ok, as long as they are relevant and look upscale.

Target Market(s)

Architecture/Business Management Consulting/Engineering Consulting

Contact Information for Business Card

dark gray background with pops of blue might be good, but you tell me. You're the designers. Rounded corners might be nice, but again, you tell me.

Font styles to use
Serif
Sans Serif

Colors
3276b5
5c5c5c
9d9d9d
fbfbfb

Requirements
Nice to have
• Something different, but still very professional.

```html
<!DOCTYPE html>
<html lang="en">
<head>
<meta charset="utf-8">
<title>Veltra Partners — Business Card</title>
<link href="https://fonts.googleapis.com/css2?family=Montserrat:wght@400;500;700;800&display=swap" rel="stylesheet">
<style>
  :root {
    --stage: #2d2d2f;
    --card: #6f6f71;
    --card-back: #676769;
    --blue: #3276b5;
    --slate: #5c5c5c;
    --mid: #9d9d9d;
    --white: #fbfbfb;
  }
  * { margin: 0; padding: 0; box-sizing: border-box; }
  html, body { width: 1200px; height: 900px; overflow: hidden; }
  body {
    background: var(--stage);
    font-family: "Montserrat", Arial, sans-serif;
    position: relative;
  }
  .card {
    position: absolute;
    left: 240px;
    width: 720px;
    height: 405px;
    border-radius: 4px;
    box-shadow: 0 14px 30px rgba(0,0,0,0.45);
  }
  .card--front { top: 30px; background: var(--card); }
  .card--back  { top: 465px; background: var(--card-back); }

  .brand {
    position: absolute;
    display: flex;
    align-items: center;
    gap: 18px;
    font-weight: 800;
    letter-spacing: 3px;
    text-transform: uppercase;
    white-space: nowrap;
  }
  .brand__mark { display: block; background: var(--blue); }
  .card--front .brand {
    left: 50%; top: 50%;
    transform: translate(-50%, -50%);
    font-size: 52px;
    color: var(--blue);
  }
  .card--front .brand__mark { width: 40px; height: 40px; }
  .card--back .brand {
    left: 48px; top: 160px;
    font-size: 30px;
    color: var(--white);
    gap: 12px;
  }
  .card--back .brand__mark { width: 24px; height: 24px; background: var(--white); }

  .contact {
    position: absolute;
    left: 405px; top: 40px;
    color: var(--white);
  }
  .contact__name { font-size: 26px; font-weight: 500; letter-spacing: 2.5px; text-transform: uppercase; }
  .contact__role { font-size: 14px; letter-spacing: 1px; margin-top: 2px; }
  .contact__rule { width: 48px; height: 2px; background: var(--white); margin: 14px 0; }
  .contact__address { font-size: 15px; line-height: 1.4; font-style: normal; letter-spacing: 0.5px; }
  .contact__list { list-style: none; font-size: 16px; letter-spacing: 0.6px; }
  .contact__list li { display: flex; align-items: center; gap: 16px; height: 31px; }
  .contact__list svg { width: 20px; height: 20px; fill: var(--white); flex: none; }
  .contact__list .plain { padding-left: 36px; }
</style>
</head>
<body>
  <section class="card card--front" aria-label="Card front">
    <div class="brand"><span class="brand__mark"></span>Veltra Partners</div>
  </section>

  <section class="card card--back" aria-label="Card back">
    <div class="brand"><span class="brand__mark"></span>Veltra</div>
    <div class="contact">
      <div class="contact__name">Daniel Morrow</div>
      <div class="contact__role">CEO | Founder</div>
      <div class="contact__rule"></div>
      <address class="contact__address">4820 Harbor Ridge Road,<br>Suite 210 Easton, NY 11900</address>
      <div class="contact__rule"></div>
      <ul class="contact__list">
        <li>
          <svg viewBox="0 0 24 24" aria-hidden="true"><path d="M6.6 10.8a15.1 15.1 0 0 0 6.6 6.6l2.2-2.2a1 1 0 0 1 1-.25 11.4 11.4 0 0 0 3.6.57 1 1 0 0 1 1 1V20a1 1 0 0 1-1 1A17 17 0 0 1 3 4a1 1 0 0 1 1-1h3.5a1 1 0 0 1 1 1c0 1.25.2 2.45.57 3.57a1 1 0 0 1-.25 1z"/></svg>
          555-014-2024
        </li>
        <li>
          <svg viewBox="0 0 24 24" aria-hidden="true"><path d="M7 2h9v5H7zM4 8h16a1 1 0 0 1 1 1v11a1 1 0 0 1-1 1H4a1 1 0 0 1-1-1V9a1 1 0 0 1 1-1zm3 3v2h3v-2zm0 4v2h3v-2zm5-4v2h5v-2zm0 4v2h5v-2z"/></svg>
          555-014-2023
        </li>
        <li>
          <svg viewBox="0 0 24 24" aria-hidden="true"><path d="M2 5h20v14H2zm2 2v.5l8 5.5 8-5.5V7zm0 2.9V17h16V9.9l-8 5.5z"/></svg>
          morrow@veltrapartners.com
        </li>
        <li>
          <svg viewBox="0 0 24 24" aria-hidden="true"><path d="M12 2a10 10 0 1 0 0 20 10 10 0 0 0 0-20zm-1 2.1V8H7.6A8 8 0 0 1 11 4.1zm2 0A8 8 0 0 1 16.4 8H13zM4.3 10H8a15 15 0 0 0 0 4H4.3a8 8 0 0 1 0-4zm5.7 0h4a13 13 0 0 1 0 4h-4a13 13 0 0 1 0-4zm6 0h3.7a8 8 0 0 1 0 4H16a15 15 0 0 0 0-4zM7.6 16H11v3.9A8 8 0 0 1 7.6 16zm5.4 0h3.4a8 8 0 0 1-3.4 3.9z"/></svg>
          www.veltrapartners.com
        </li>
        <li class="plain">www.veltrapartners.com</li>
      </ul>
    </div>
  </section>
</body>
</html>
```